High end Electrical/home automation Business Card

Need a card for a high end electrical and home automation company utilising the existing logo.
Phone
Email
Website

Like black look with raised detail. Don’t necessarily need to keep colour of logo it could be made grayscale or white etc

Target Market(s)

High end clients

Contact Information for Business Card

Brightmoor Electrical

Requirements
Must have
• Logo, phone, email, website, address

High end look
Nice to have
• Black background card
Raised font
Should not have
• Lots of colour

```html
<!DOCTYPE html>
<html lang="en">
<head>
<meta charset="utf-8">
<title>Brightmoor Electrical – Business Card</title>
<link href="https://fonts.googleapis.com/css2?family=Montserrat:wght@400;500;700&display=swap" rel="stylesheet">
<style>
  :root {
    --backdrop: #b1b1ad;
    --card-dark: #38383a;
    --card-light: #ffffff;
    --accent: #0a93d8;
    --text-light: #f2f2f2;
    --emboss: #4a4a4d;
  }
  * { margin: 0; padding: 0; box-sizing: border-box; }
  html, body {
    width: 1200px; height: 801px; overflow: hidden;
    background: var(--backdrop);
    font-family: "Montserrat", Arial, sans-serif;
  }
  .stage { position: relative; width: 1200px; height: 801px; }
  .card {
    position: absolute; top: 246px;
    width: 540px; height: 309px;
    background: var(--card-dark);
    border-bottom: 5px solid var(--accent);
    overflow: hidden;
    box-shadow: 0 14px 28px rgba(0,0,0,0.22);
  }
  .card--front { left: 40px; }
  .card--back { left: 620px; }

  .front__panel {
    position: absolute; inset: 0;
    background: var(--card-light);
    clip-path: polygon(300px 0, 540px 0, 540px 309px, 380px 309px);
  }
  .front__mark {
    position: absolute; left: 372px; top: 118px; width: 150px;
    color: var(--accent); font-weight: 700; font-size: 19px; line-height: 1.25;
    text-align: center;
  }
  .front__brand {
    position: absolute; left: 28px; top: 34px;
    color: var(--text-light); font-weight: 700; font-size: 19px; letter-spacing: -0.2px;
  }
  .front__person { position: absolute; left: 28px; top: 118px; }
  .person__name {
    color: var(--accent); font-weight: 500; font-size: 19px; letter-spacing: 1.5px;
    text-transform: uppercase;
  }
  .person__role { color: var(--text-light); font-size: 12px; margin-top: 2px; }
  .contact { list-style: none; margin-top: 14px; color: var(--text-light); font-size: 12px; line-height: 1.55; }
  .contact li { display: flex; align-items: center; gap: 6px; }
  .contact svg { width: 10px; height: 10px; fill: var(--accent); flex: none; }
  .contact .no-icon { padding-left: 16px; }
  .front__tab {
    position: absolute; left: 0; bottom: 0; width: 26px; height: 14px;
    background: var(--accent);
  }

  .back__mark {
    position: absolute; inset: 0;
    display: flex; align-items: center; justify-content: center;
    color: var(--emboss); font-weight: 700; font-size: 32px;
  }
</style>
</head>
<body>
<main class="stage">
  <section class="card card--front" aria-label="Card front">
    <div class="front__panel"></div>
    <div class="front__mark">Brightmoor Electrical</div>
    <div class="front__brand">Brightmoor Electrical</div>
    <div class="front__person">
      <p class="person__name">Daniel Hartley</p>
      <p class="person__role">Founder</p>
      <ul class="contact">
        <li class="no-icon">418 Alder Lane</li>
        <li class="no-icon">Colville, WA 99114</li>
        <li><svg viewBox="0 0 10 10"><path d="M2 0.5l2 2-1 1.2c.6 1.3 1.6 2.3 2.9 2.9L7.1 5.6l2 2-1.3 1.9C4.3 9.3.7 5.7.5 2.2z"/></svg>509 555 0182</li>
        <li><svg viewBox="0 0 10 10"><path d="M0 2h10v6H0zM1 3v.4L5 6l4-2.6V3L5 5.6z"/></svg>hello@brightmoor.com</li>
        <li><svg viewBox="0 0 10 10"><circle cx="5" cy="5" r="4.5"/></svg>brightmoorelectrical.com</li>
      </ul>
    </div>
    <div class="front__tab"></div>
  </section>

  <section class="card card--back" aria-label="Card back">
    <div class="back__mark">Brightmoor Electrical</div>
  </section>
</main>
</body>
</html>
```